IT company developing solutions for air cargo industry is looking for a new website

We are a professional IT company developing solutions for air cargo industry worldwide.

We are looking to update and completely redesign our current webpages: https://www.brisklane.cz/

What we like about our current pages are the animated graphics on the home page. These could stay, but not a must.

The design of the new pages should be very modern, clean, unique, creative, professional, and to make a statement. We are looking for animated graphics, cool and interesting interactions, cascading layers, etc.

Our company logo is yellow, gray and black. You don’t necessarily have to stick to this colour scheme, however the corporate colors should work well with the overal design of the web pages.
Dark mode pages are also an option.

The scope of the project would include creating a:

• Header
• Footer
• Landing page
• Navigation bar (8 tabs)
• Subpages (10)

In the first stage we are looking only for the header / footer / landing page with navigaton bar / Solutions page design.
As a second round, finalists might be asked to submit another section of the website to see their consistency in terms of the look and feel proposed for the Homepage and Solutions’ pages.
The winning designer will then complete the rest of the pages.

Attached you will find a brief for the first scope of the project. Please read the note section on slide nr. 3 carefully to understand, what we exactly are looking for to achieve.

Industry/Entity Type

Aviation

Number of Pages Required

1 page

Requirements
Must have
• See brief
Nice to have
• See brief
Should not have
• See brief

```html
<!DOCTYPE html>
<html lang="en">
<head>
<meta charset="utf-8">
<title>Brisk Lane – IT Solutions for Air Cargo</title>
<link rel="stylesheet" href="https://fonts.googleapis.com/css2?family=Lato:wght@400;700&family=Open+Sans:wght@400;500;600;700&display=swap">
<style>
  :root {
    --gold: #ffc20e;
    --ink: #111111;
    --nav: #262626;
    --hero: #070b1a;
    --facts: #121212;
    --footer: #0b0b0b;
    --white: #ffffff;
    --line: #3a3a30;
  }
  * { margin: 0; padding: 0; box-sizing: border-box; }
  html, body { width: 824px; height: 1200px; overflow: hidden; background: var(--footer); }
  body { font-family: "Lato", sans-serif; color: var(--white); position: relative; }

  .promo-bar {
    height: 35px; background: var(--gold); color: var(--ink);
    font-size: 10.5px; font-weight: 700; display: flex; align-items: center; justify-content: center;
  }

  .site-nav {
    height: 47px; background: var(--nav); display: flex; align-items: center; padding: 0 0 0 61px;
  }
  .brand { display: flex; align-items: center; gap: 6px; font-family: "Lato", sans-serif; font-weight: 700; color: var(--white); }
  .brand-mark { background: var(--gold); }
  .site-nav .brand { font-size: 16px; }
  .site-nav .brand-mark { width: 10px; height: 10px; }
  .nav-links { display: flex; list-style: none; margin-left: 121px; }
  .nav-links li { font-size: 9px; margin-right: 25.5px; display: flex; align-items: center; gap: 4px; }
  .caret { width: 0; height: 0; border-left: 3px solid transparent; border-right: 3px solid transparent; border-top: 3px solid var(--white); margin-top: 3px; }

  .hero { height: 379px; position: relative; overflow: hidden; background: var(--hero); }
  .hero-shade { position: absolute; left: 0; top: 0; width: 102px; height: 355px; background: #000; }
  .hero-visual {
    position: absolute; left: 390px; top: 0; width: 434px; height: 379px;
    background: linear-gradient(135deg, #14284a 0%, #1a4a78 45%, #0d1c3a 100%);
  }
  .hero-copy { position: absolute; left: 77px; top: 73px; width: 300px; }
  .hero-title { font-weight: 400; font-size: 20px; line-height: 35px; white-space: nowrap; }
  .hero-title mark { background: var(--gold); color: var(--ink); padding: 0 2px; }
  .hero-text { font-size: 8.8px; line-height: 20px; margin-top: 10px; white-space: nowrap; }
  .btn-primary {
    display: inline-block; margin-top: 16px; background: var(--gold); color: var(--ink);
    font-family: "Open Sans", sans-serif; font-weight: 600; font-size: 12px;
    width: 103px; height: 35px; line-height: 35px; text-align: center;
  }

  .statement {
    height: 129px; background: var(--gold); color: var(--ink);
    font-family: "Open Sans", sans-serif; font-weight: 700; font-size: 21px; line-height: 35px;
    display: flex; align-items: center; justify-content: center; text-align: center; padding: 0 90px;
  }

  .facts { height: 397px; background: var(--facts); padding-top: 33px; }
  .facts-title { font-family: "Open Sans", sans-serif; font-weight: 600; font-size: 27px; color: var(--gold); text-align: center; }
  .facts-grid {
    margin: 25px 0 0 77px; width: 670px; display: grid; grid-template-columns: repeat(3, 1fr);
    grid-template-rows: 120px 118px; border: 1px solid var(--line);
  }
  .fact { border-right: 1px solid var(--line); display: flex; flex-direction: column; align-items: center; justify-content: center; text-align: center; font-family: "Open Sans", sans-serif; }
  .fact:nth-child(3n) { border-right: none; }
  .fact:nth-child(-n+3) { border-bottom: 1px solid var(--line); }
  .fact-value { color: var(--gold); font-size: 27px; font-weight: 500; line-height: 32px; }
  .fact-label { font-size: 15px; font-weight: 500; line-height: 21px; margin-top: 10px; }

  .site-footer { height: 213px; background: var(--footer); text-align: center; padding-top: 55px; }
  .site-footer .brand { justify-content: center; font-size: 28px; gap: 10px; }
  .site-footer .brand-mark { width: 18px; height: 18px; }
  .footer-links { display: flex; justify-content: center; list-style: none; gap: 29px; margin-top: 34px; font-size: 10.5px; }
  .copyright { font-size: 10.5px; margin-top: 33px; }
</style>
</head>
<body>
  <div class="promo-bar">Affordable IT Solutions That Revolutionize Tomorrow's Air Cargo Today</div>

  <nav class="site-nav">
    <div class="brand">Brisk Lane <span class="brand-mark"></span></div>
    <ul class="nav-links">
      <li>Industries</li>
      <li>Solutions <span class="caret"></span></li>
      <li>Operational Support</li>
      <li>Case Studies</li>
      <li>Testimonials</li>
      <li>News</li>
      <li>About Us <span class="caret"></span></li>
    </ul>
  </nav>

  <section class="hero">
    <div class="hero-shade"></div>
    <div class="hero-visual" role="img" aria-label="Night view of the Earth with a connected network and cargo route pins"></div>
    <div class="hero-copy">
      <h1 class="hero-title">Seamlessly connecting the air<br>cargo industry from <mark>Manila</mark><br><mark>to Tahiti</mark></h1>
      <p class="hero-text">Blending decades of air cargo knowledge with end-to-end IT solutions.<br>Whether you are an Airline, GSA, GHA, Forwarder or E-commerce<br>Operator,our expertise can elevate your daily workflows, cutting down<br>on expenses, time, and errors.</p>
      <a class="btn-primary">Learn More</a>
    </div>
  </section>

  <section class="statement">We are not IT tech experts attempting to do cargo! We are cargo experts with programming</section>

  <section class="facts">
    <h2 class="facts-title">Our Facts</h2>
    <div class="facts-grid">
      <div class="fact"><div class="fact-value">2014</div><div class="fact-label">Established</div></div>
      <div class="fact"><div class="fact-value">22</div><div class="fact-label">Employees</div></div>
      <div class="fact"><div class="fact-value">11,500,000 +</div><div class="fact-label">Nr. of Annual Electronic<br>Exchanges</div></div>
      <div class="fact"><div class="fact-value">18</div><div class="fact-label">Countries covered</div></div>
      <div class="fact"><div class="fact-value">20+</div><div class="fact-label">Connected Clients</div></div>
      <div class="fact"><div class="fact-value">350,000+</div><div class="fact-label">Nr. of Annual AWBs</div></div>
    </div>
  </section>

  <footer class="site-footer">
    <div class="brand">Brisk Lane <span class="brand-mark"></span></div>
    <ul class="footer-links">
      <li>Industries</li>
      <li>Solutions</li>
      <li>Operational Support</li>
      <li>Case Studies</li>
      <li>Testimonials</li>
      <li>News</li>
      <li>About Us</li>
    </ul>
    <p class="copyright">Copyrights@2024.Brisk Lane.All Rights Reserved</p>
  </footer>
</body>
</html>
```